Building company buisness cards

We are looking for a sharp modern new look for our business cards.
We are a New Zealand based company that specialises in house and land packages.
We have attached a photo of the current logo and would like to see if it can be improved somehow if needed.
We are open to any colours but we have chosen green at this stage.
Feel free to change the font and make the logo smarter looking.
Play with the colours and see what looks best.

We want a card that looks so good know one will want to throw it away!

Target Market(s)

Home buyers

Industry/Entity Type

Building

Contact Information for Business Card

Derek Tolvane
0217394062
dtolvane@quillmarkhomesteads.co.nz
quillmarkhomesteads.co.nz

Font styles to use
Serif
Sans Serif

Colors

Designer to choose colors to be used in the design.

Requirements
Must have
• Logo and company name on one side, details on the other side
Nice to have
• Color codes for the original green are HEX #4a8028, RGB(74,128,40), CMYK(42,0,69,50)
• Round corners, Raised and/or spot UV

```html
<!DOCTYPE html>
<html lang="en">
<head>
<meta charset="utf-8">
<title>Quillmark Homesteads – Business Cards</title>
<link rel="stylesheet" href="https://fonts.googleapis.com/css2?family=Montserrat:wght@600;800&family=Open+Sans:wght@400&display=swap">
<style>
  :root {
    --brand-green: #4a8a1f;
    --paper-white: #ffffff;
    --swoosh-grey: #8a8a8a;
    --rule-grey: #b9b9b9;
    --backdrop: #2c2c2c;
  }
  html, body {
    margin: 0;
    width: 1200px;
    height: 900px;
    overflow: hidden;
    background: var(--backdrop);
  }
  .canvas {
    position: relative;
    width: 1200px;
    height: 900px;
  }
  .card {
    position: absolute;
    width: 620px;
    height: 354px;
    border-radius: 18px;
    overflow: hidden;
  }
  .card--front { left: 90px; top: 80px; background: var(--paper-white); }
  .card--back  { left: 490px; top: 466px; background: var(--brand-green); }

  .card__shapes { position: absolute; inset: 0; }
  .swoosh-grey  { fill: var(--swoosh-grey); }
  .swoosh-green { fill: var(--brand-green); }

  .wordmark {
    position: absolute;
    font-family: "Montserrat", sans-serif;
    font-weight: 800;
    line-height: 0.95;
    letter-spacing: -0.5px;
    display: flex;
    align-items: center;
    gap: 12px;
  }
  .wordmark__dot {
    width: 22px; height: 22px;
    border-radius: 50%;
    flex: none;
  }
  .wordmark__rule {
    position: absolute;
    height: 1px;
    background: var(--rule-grey);
  }

  .card--front .wordmark { left: 36px; top: 118px; color: var(--brand-green); font-size: 32px; }
  .card--front .wordmark__dot { background: var(--brand-green); }
  .card--front .wordmark__rule { left: 110px; top: 210px; width: 80px; }

  .card--back .wordmark { left: 0; right: 0; top: 128px; justify-content: center; color: var(--paper-white); font-size: 44px; }
  .card--back .wordmark__dot { background: var(--paper-white); width: 26px; height: 26px; }
  .card--back .wordmark__rule { left: 270px; top: 252px; width: 80px; background: rgba(255,255,255,0.6); }

  .contact {
    position: absolute;
    right: 26px;
    top: 34px;
    text-align: right;
    color: var(--paper-white);
    font-family: "Open Sans", sans-serif;
    font-size: 11.5px;
  }
  .contact__name {
    font-family: "Montserrat", sans-serif;
    font-weight: 600;
    font-size: 18px;
    margin: 0 0 12px;
  }
  .contact__line {
    display: flex;
    justify-content: flex-end;
    align-items: center;
    gap: 7px;
    margin: 0 0 4px;
  }
  .contact__icon { width: 11px; height: 11px; flex: none; }
  .contact__stack {
    position: absolute;
    right: 26px;
    bottom: 34px;
    text-align: right;
    color: var(--paper-white);
    font-family: "Open Sans", sans-serif;
    font-size: 13.5px;
    line-height: 1.35;
  }
</style>
</head>
<body>
<main class="canvas">

  <section class="card card--front" aria-label="Business card, details side">
    <svg class="card__shapes" viewBox="0 0 620 354" width="620" height="354" aria-hidden="true">
      <path class="swoosh-grey" d="M346,96 C338,238 238,322 82,354 L220,354 Z"/>
      <path class="swoosh-green" d="M340,0 C350,170 270,300 120,354 L620,354 L620,0 Z"/>
    </svg>

    <div class="wordmark">
      <span class="wordmark__dot"></span>
      <span>quillmark<br>homesteads.</span>
    </div>
    <div class="wordmark__rule"></div>

    <div class="contact">
      <p class="contact__name">Derek Tolvane</p>
      <p class="contact__line">0217394062
        <svg class="contact__icon" viewBox="0 0 12 12"><path fill="#fff" d="M2.5,1 L4.5,1 L5.2,3.6 L3.9,4.5 C4.6,6 5.9,7.3 7.4,8 L8.4,6.8 L11,7.5 L11,9.5 C11,10.3 10.3,11 9.5,11 C5,11 1,7 1,2.5 C1,1.7 1.7,1 2.5,1 Z"/></svg>
      </p>
      <p class="contact__line">dtolvane@quillmarkhomesteads.co.nz
        <svg class="contact__icon" viewBox="0 0 12 12"><rect x="1" y="2.5" width="10" height="7" fill="#fff"/><path d="M1,2.5 L6,6.5 L11,2.5" stroke="#4a8a1f" stroke-width="1" fill="none"/></svg>
      </p>
      <p class="contact__line">quillmarkhomesteads.co.nz
        <svg class="contact__icon" viewBox="0 0 12 12"><circle cx="6" cy="6" r="5" fill="none" stroke="#fff" stroke-width="1.2"/><ellipse cx="6" cy="6" rx="2.2" ry="5" fill="none" stroke="#fff" stroke-width="1"/><line x1="1" y1="6" x2="11" y2="6" stroke="#fff" stroke-width="1"/></svg>
      </p>
    </div>

    <div class="contact__stack">
      dtolvane@quillmarkhomesteads.co.nz<br>
      www.quillmarkhomesteads.co.nz
    </div>
  </section>

  <section class="card card--back" aria-label="Business card, logo side">
    <div class="wordmark">
      <span class="wordmark__dot"></span>
      <span>quillmark<br>homesteads.</span>
    </div>
    <div class="wordmark__rule"></div>
  </section>

</main>
</body>
</html>
```